CBD AgriBusiness Verdant Trophy Business Card

We are HiTec producer of medical cannabis CBD Switzerland of high quality. Our website is alpinleaf.net, we will also revisit it graphically, the winner of this contest will be the graphic designer chosen for the new design of the website. We stand out by the skill of the team, many of our engineers we win cup cannabis. I join the current map to take as an example but to revisit completely: deletion of surname and first name, modification of funds (front / back), reorganization of text info, highlighting the address of the website. three characteristics define the business card: Professional, Class, refined. The business card must be optimized for soft-touch and selective varnish printing.

Target Market(s)

Customers and Suppliers

Industry/Entity Type

Agribusiness

Contact Information for Business Card

Logo, Tél / Whatsapp, mail, url du site : alpinleaf.net

Font styles to use
Sans Serif

Requirements
Must have
• Logo of alpinleaf.net
Nice to have
• a design that stands out well on the selective varnish
Should not have
• Last name and first name

```html
<!DOCTYPE html>
<html lang="en">
<head>
<meta charset="utf-8">
<title>alpinleaf business card</title>
<link rel="stylesheet" href="https://fonts.googleapis.com/css2?family=Work+Sans:wght@400;500;600&display=swap">
<style>
  :root {
    --backdrop: #141414;
    --card: #262626;
    --card-edge: #2e2e2e;
    --varnish: #3a3a3a;
    --ink: #f2f2f2;
    --ink-soft: #c9c9c9;
  }
  * { margin: 0; padding: 0; box-sizing: border-box; }
  html, body { width: 1200px; height: 900px; overflow: hidden; }
  body {
    background: var(--backdrop);
    font-family: "Work Sans", sans-serif;
    position: relative;
  }
  .card {
    position: absolute;
    left: 250px;
    width: 700px;
    height: 400px;
    background: var(--card);
    border: 1px solid var(--card-edge);
    box-shadow: 0 18px 40px rgba(0,0,0,0.55);
  }
  .card--front { top: 36px; }
  .card--back { top: 464px; }

  .brand {
    display: flex;
    align-items: center;
    gap: 12px;
    font-weight: 600;
    letter-spacing: -1px;
    color: var(--varnish);
  }
  .brand__mark {
    width: 30px;
    height: 30px;
    background: var(--varnish);
  }
  .card--front .brand {
    position: absolute;
    top: 50%;
    left: 50%;
    transform: translate(-50%, -50%);
    font-size: 68px;
  }
  .card--back .brand {
    position: absolute;
    top: 50%;
    left: 40px;
    transform: translateY(-50%);
    font-size: 52px;
  }
  .card--back .brand__mark { width: 24px; height: 24px; }

  .divider {
    position: absolute;
    left: 370px;
    top: 48px;
    width: 1px;
    height: 304px;
    background: var(--ink-soft);
  }
  .contact {
    position: absolute;
    left: 400px;
    top: 48px;
    height: 304px;
    display: flex;
    flex-direction: column;
    justify-content: center;
    color: var(--ink);
    letter-spacing: 1px;
  }
  .contact__role {
    font-size: 15px;
    color: var(--ink-soft);
    text-transform: uppercase;
    letter-spacing: 2px;
    margin-bottom: 18px;
  }
  .contact__address {
    font-size: 16px;
    line-height: 1.45;
    margin-bottom: 18px;
  }
  .contact__list { list-style: none; font-size: 17px; line-height: 1.6; }
  .contact__list li { display: flex; align-items: center; gap: 12px; }
  .contact__list svg { width: 12px; height: 12px; flex: none; fill: none; stroke: var(--ink-soft); stroke-width: 1.6; }
  .contact__list .contact__web {
    margin-top: 12px;
    font-size: 21px;
    font-weight: 600;
    letter-spacing: 0.5px;
  }
  .contact__web svg { width: 15px; height: 15px; stroke: var(--ink); }
</style>
</head>
<body>
  <section class="card card--front">
    <div class="brand"><span class="brand__mark"></span>alpinleaf</div>
  </section>

  <section class="card card--back">
    <div class="brand"><span class="brand__mark"></span>alpinleaf</div>
    <div class="divider"></div>
    <div class="contact">
      <p class="contact__role">Director</p>
      <p class="contact__address">42 Harbour Lane,<br>Westfield, NZ, 8020</p>
      <ul class="contact__list">
        <li><svg viewBox="0 0 12 12"><path d="M2 1.5 L4 1.5 L5 4 L3.8 5 Q5 7.5 7 8.2 L8 7 L10.5 8 L10.5 10 Q5 10.5 1.5 2 Z"/></svg>+41 (0) 70 555 01 23</li>
        <li><svg viewBox="0 0 12 12"><rect x="3" y="1" width="6" height="10" rx="1"/><line x1="5" y1="9" x2="7" y2="9"/></svg>+44 7700 90 01 45</li>
        <li><svg viewBox="0 0 12 12"><rect x="1" y="2.5" width="10" height="7"/><path d="M1 2.5 L6 6.5 L11 2.5"/></svg>office@alpinleaf.net</li>
        <li class="contact__web"><svg viewBox="0 0 12 12"><circle cx="6" cy="6" r="5"/><ellipse cx="6" cy="6" rx="2.2" ry="5"/><line x1="1" y1="6" x2="11" y2="6"/></svg>www.alpinleaf.net</li>
      </ul>
    </div>
  </section>
</body>
</html>
```